Business Card Design

WE are looking for a premium quality Business Cards for a Law Firm . Copies of our current business card is attached.

Contact Information for Business Card

xyz

```html
<!DOCTYPE html>
<html lang="en">
<head>
<meta charset="utf-8">
<title>Ashford Lawyers – Business Card</title>
<link rel="stylesheet" href="https://fonts.googleapis.com/css2?family=Lato:wght@400;700;900&display=swap">
<style>
  :root {
    --stage: #2c2f34;
    --paper: #ffffff;
    --forest: #0f2a1e;
    --gold: #c9a15a;
    --ink-grey: #555a5e;
    --rule-grey: #9a9a9a;
  }
  * { box-sizing: border-box; margin: 0; padding: 0; }
  html, body {
    width: 1200px; height: 952px; overflow: hidden;
    background: var(--stage);
    font-family: "Lato", Arial, sans-serif;
  }
  .stage {
    position: relative; width: 1200px; height: 952px;
    display: flex; align-items: center; justify-content: center; gap: 60px;
  }
  .card {
    position: relative; width: 500px; height: 305px;
    border-radius: 22px; overflow: hidden;
  }

  /* Front */
  .card--front { background: var(--paper); }
  .brand {
    position: absolute; left: 30px; top: 34px;
    display: flex; align-items: center; gap: 10px;
  }
  .brand__dot {
    width: 30px; height: 30px; border-radius: 50%;
    border: 2px solid var(--gold);
  }
  .brand__name {
    font-weight: 700; font-size: 20px; letter-spacing: 2px;
    color: var(--forest);
  }
  .contacts {
    position: absolute; left: 30px; top: 104px;
    list-style: none; display: flex; flex-direction: column; gap: 7px;
  }
  .contacts li {
    display: flex; align-items: center; gap: 8px;
    font-size: 11.5px; color: var(--ink-grey);
  }
  .contacts svg { width: 15px; height: 15px; flex: none; }
  .holder {
    position: absolute; right: 32px; top: 112px; text-align: right;
  }
  .holder__name {
    font-weight: 900; font-size: 25px; letter-spacing: 0.5px;
    color: var(--forest);
  }
  .holder__role, .holder__cred {
    font-size: 11px; color: var(--gold); letter-spacing: 0.4px; margin-top: 3px;
  }
  .holder__role { font-weight: 700; }
  .holder__rule {
    width: 62px; height: 1px; background: var(--rule-grey);
    margin: 10px 0 0 auto;
  }
  .emblem-ring {
    position: absolute; left: 160px; top: 190px;
    width: 200px; height: 200px; border-radius: 50%;
    border: 5px solid var(--gold); opacity: 0.85;
  }

  /* Back */
  .card--back {
    background: var(--forest);
    display: flex; flex-direction: column; align-items: center; justify-content: center;
    color: var(--gold);
  }
  .back-brand__dot {
    width: 52px; height: 52px; border-radius: 50%;
    border: 2px solid var(--gold); margin-bottom: 12px;
  }
  .back-brand__name {
    font-weight: 700; font-size: 26px; letter-spacing: 3px;
  }
  .address {
    font-style: normal; text-align: center; font-size: 11.5px;
    line-height: 1.5; margin-top: 14px; letter-spacing: 0.3px;
  }
</style>
</head>
<body>
<main class="stage">
  <section class="card card--front" aria-label="Business card front">
    <div class="brand">
      <span class="brand__dot"></span>
      <span class="brand__name">ASHFORD LAWYERS</span>
    </div>

    <ul class="contacts">
      <li>
        <svg viewBox="0 0 16 16"><rect width="16" height="16" rx="3" fill="#0f2a1e"/><path d="M5 4c1 0 1.5 2 1 2.5L5.5 7c.6 1.4 1.6 2.4 3 3l.5-.5c.5-.5 2.5 0 2.5 1 0 .8-1 1.5-2 1.5C6.5 12 4 9.5 4 6.5 4 5 4.3 4 5 4z" fill="#fff"/></svg>
        +61 7 3000 4812
      </li>
      <li>
        <svg viewBox="0 0 16 16"><rect width="16" height="16" rx="3" fill="#0f2a1e"/><rect x="5.5" y="3" width="5" height="10" rx="1" fill="none" stroke="#fff" stroke-width="1.2"/><circle cx="8" cy="11.3" r=".6" fill="#fff"/></svg>
        +61 0400 123 456
      </li>
      <li>
        <svg viewBox="0 0 16 16"><rect width="16" height="16" rx="3" fill="#0f2a1e"/><rect x="3.5" y="5" width="9" height="6.5" fill="none" stroke="#fff" stroke-width="1.1"/><path d="M3.5 5l4.5 3.5L12.5 5" fill="none" stroke="#fff" stroke-width="1.1"/></svg>
        daniel@ashfordlawyers.com.au
      </li>
      <li>
        <svg viewBox="0 0 16 16"><rect width="16" height="16" rx="3" fill="#0f2a1e"/><circle cx="8" cy="8" r="4.3" fill="none" stroke="#fff" stroke-width="1.1"/><path d="M3.7 8h8.6M8 3.7c-2 2.4-2 6.2 0 8.6M8 3.7c2 2.4 2 6.2 0 8.6" fill="none" stroke="#fff" stroke-width=".9"/></svg>
        www.ashfordlawyers.com.au
      </li>
    </ul>

    <div class="holder">
      <h1 class="holder__name">DANIEL MOREAU</h1>
      <p class="holder__role">DIRECTOR &amp; PRINCIPAL SOLICITOR</p>
      <p class="holder__cred">MBA, Juris Doctor</p>
      <div class="holder__rule"></div>
    </div>

    <div class="emblem-ring"></div>
  </section>

  <section class="card card--back" aria-label="Business card back">
    <span class="back-brand__dot"></span>
    <span class="back-brand__name">ASHFORD LAWYERS</span>
    <address class="address">
      Level 3, Ashford House, 210 Harbour Terrace<br>
      Riverside, QLD 4100
    </address>
  </section>
</main>
</body>
</html>
```